Design a product reviews website

We need a website design and simple logo for the brand Venlotix.com. The website will provide reviews of technology products and services. The brand and website should be approachable but should also be trustworthy and high quality. The deliverable should be designs, specs and assets that I can provide to a development team to build the website.

Target Market(s)

People researching products to buy.

Industry/Entity Type

Product

Logo Text

Venlotix.com

Number of Pages Required

5+ page

Font styles to use
Sans Serif

Colors
0492cd
0355a3
3176b5
33a6d7
85cae6
85abd2
cedeed
cee9f5

Requirements
Must have
• - Designs for the Homepage, Category and Article pages.
• - Designs for web and mobile.
• - Designs details for the engineering team to use for development.
• - I'm open to other colors than the preferences I chose but I'm more likely to like blues, greys and blacks.

```html
<!DOCTYPE html>
<html lang="en">
<head>
<meta charset="utf-8">
<title>Venlotix.com – Product Reviews</title>
<link rel="stylesheet" href="https://fonts.googleapis.com/css2?family=Lato:wght@400;700&family=Questrial&family=Roboto+Condensed:wght@300;400&display=swap">
<style>
:root{
  --blue:#3b87de;
  --blue-dark:#2f74c6;
  --page:#eceef1;
  --panel:#ffffff;
  --line:#d9dce0;
  --text:#333a40;
  --muted:#5d646b;
  --footer:#232527;
  --loadbar:#8b8e91;
}
*{margin:0;padding:0;box-sizing:border-box}
html,body{width:832px;height:1200px;overflow:hidden}
body{position:relative;background:linear-gradient(160deg,#f1f2f4,#e3e5e8 60%,#eef0f2);font-family:"Lato",sans-serif;color:var(--text)}
.abs{position:absolute}
/* header */
.site-header{left:0;top:0;width:832px;height:40px;background:#fafafa}
.brand{left:47px;top:11px}
.brand-name{font-family:"Lato",sans-serif;font-size:18px;line-height:22px;color:#3a3f44;font-weight:400;letter-spacing:.1px}
.search{left:493px;top:8px;width:244px;height:24px;display:flex;border:1px solid var(--line);background:#fff}
.search-input{flex:1;font-size:8.5px;color:#7a7f84;padding:6px 0 0 12px}
.search-btn{width:30px;background:var(--blue);display:flex;align-items:center;justify-content:center}
.menu-btn{left:759px;top:8px;width:28px;height:24px;border:1px solid #444;border-radius:2px;display:flex;flex-direction:column;justify-content:center;align-items:center;gap:2px;background:#fff}
.menu-btn span{width:14px;height:1.5px;background:#333}
/* hero */
.hero{left:0;top:40px;width:832px;height:275px;background:linear-gradient(100deg,#d8d6d0 0%,#c9c4bb 35%,#8b8b8c 55%,#e5e5e3 75%,#bfc1c3 100%)}
.hero-caption{left:46px;top:118px;width:336px;height:80px;background:rgba(255,255,255,.55);padding:12px 0 0 8px;font-family:"Questrial",sans-serif;font-size:23px;line-height:26px;color:#222}
.hero-dots{left:48px;top:229px;display:flex;gap:4px}
.hero-dots span{width:6px;height:6px;border-radius:50%;background:#fff}
.hero-dots span.on{background:var(--blue);box-shadow:0 0 0 1px #fff}
/* sidebar */
.category-nav{left:47px;top:339px;width:139px;background:#f7f8f9;border:1px solid var(--line)}
.category-nav a{display:flex;align-items:center;height:33.6px;border-top:1px solid var(--line);font-size:9.5px;color:#333;text-decoration:none;letter-spacing:-.1px}
.category-nav a:first-child{border-top:none;background:var(--blue);color:#fff}
.category-nav svg{width:22px;height:20px;margin:0 12px 0 7px}
/* panels */
.panel{background:#f9f9fa;border:1px solid var(--line)}
.panel-title{height:30px;border-bottom:1px solid var(--line);font-family:"Roboto Condensed",sans-serif;font-weight:300;font-size:13px;padding:8px 0 0 16px;color:#333;background:#f6f6f7}
.new-products{left:209px;top:339px;width:375px;height:762px}
.popular-products{left:607px;top:339px;width:180px;height:762px}
.card{background:#fff}
.photo{position:relative;display:block}
.tags{position:absolute;right:10px;bottom:10px;display:flex;gap:4px}
.tag{background:var(--blue);color:#fff;font-size:10px;height:22px;padding:5px 9px 0;letter-spacing:.2px}
.card-title{font-family:"Roboto Condensed",sans-serif;font-weight:300;font-size:13.5px;color:#333;line-height:17.6px}
.feature .card-title{padding:11px 8px 9px;border-bottom:1px solid #e7e8ea;margin:0 7px 0 0}
.byline{display:flex;align-items:center;padding:5px 11px 0 8px;height:37px}
.avatar{width:29px;height:29px;background:linear-gradient(#cfd6dd,#9aa5b0)}
.author{font-size:12px;color:var(--blue);margin-left:6px;flex:1}
.posted{font-size:8px;font-style:italic;color:#555}
.mini .card-title{padding:8px 6px 6px}
.pop .card-title{padding:10px 8px 6px;font-size:13px}
/* load more + footer */
.load-more{left:210px;top:1115px;width:577px;height:33px;background:var(--loadbar);color:#fff;font-size:11px;font-weight:700;display:flex;align-items:center;justify-content:center;gap:7px}
.site-footer{left:0;top:1166px;width:832px;height:34px;background:var(--footer);color:#eee;font-size:9.5px;display:flex;align-items:center;justify-content:center}
</style>
</head>
<body>

<header class="site-header abs">
  <div class="brand abs"><div class="brand-name">Venlotix.com</div></div>
  <div class="search abs">
    <div class="search-input">Search for products</div>
    <div class="search-btn"><svg width="10" height="10" viewBox="0 0 10 10"><circle cx="4" cy="4" r="3" fill="none" stroke="#fff" stroke-width="1.3"/><line x1="6.2" y1="6.2" x2="9" y2="9" stroke="#fff" stroke-width="1.3"/></svg></div>
  </div>
  <div class="menu-btn abs"><span></span><span></span><span></span></div>
</header>

<section class="hero abs" role="img" aria-label="Security cameras and a monitoring screen in a bright living room"></section>
<div class="hero-caption abs">The Best Product and Services<br>Reviews and Rankings</div>
<div class="hero-dots abs"><span class="on"></span><span></span><span></span><span></span></div>

<nav class="category-nav abs">
  <a href="#"><svg viewBox="0 0 22 20"><path d="M11 2 2 10h3v8h4v-5h4v5h4v-8h3z" fill="#fff"/></svg>HOME</a>
  <a href="#"><svg viewBox="0 0 22 20"><rect x="6" y="1" width="11" height="18" rx="2" fill="#444"/><rect x="9" y="8" width="6" height="5" fill="#f7f8f9"/></svg>APPLIANCES</a>
  <a href="#"><svg viewBox="0 0 22 20"><rect x="3" y="2" width="16" height="11" fill="none" stroke="#444" stroke-width="1.4"/><line x1="8" y1="17" x2="14" y2="17" stroke="#444" stroke-width="1.4"/></svg>COMPUTERS</a>
  <a href="#"><svg viewBox="0 0 22 20"><rect x="1" y="4" width="20" height="12" rx="2" fill="none" stroke="#444" stroke-width="1.4"/><circle cx="15" cy="10" r="3" fill="none" stroke="#444" stroke-width="1.4"/><line x1="4" y1="8" x2="9" y2="8" stroke="#444"/><line x1="4" y1="12" x2="9" y2="12" stroke="#444"/></svg>ELECTRONICS</a>
  <a href="#"><svg viewBox="0 0 22 20"><path d="M2 10 10 3l8 7M4 9v9h10" fill="none" stroke="#444" stroke-width="1.2"/><path d="M14 8l4 1.5v4c0 2-2 3.5-4 4.5-2-1-4-2.5-4-4.5v-4z" fill="none" stroke="#444" stroke-width="1.2"/></svg>HOME SECURITY</a>
  <a href="#"><svg viewBox="0 0 22 20"><rect x="7" y="1" width="8" height="18" rx="1.5" fill="none" stroke="#444" stroke-width="1.4"/></svg>MOBILES</a>
  <a href="#"><svg viewBox="0 0 22 20"><path d="M3 9 11 2l8 7v9H3z" fill="none" stroke="#444" stroke-width="1.2"/><circle cx="11" cy="12" r="2.5" fill="none" stroke="#444"/></svg>SMART HOME</a>
  <a href="#"><svg viewBox="0 0 22 20"><rect x="6" y="5" width="10" height="10" fill="none" stroke="#444" stroke-width="1.2"/><rect x="9" y="8" width="4" height="4" fill="#444"/><path d="M8 2v3M11 2v3M14 2v3M8 15v3M11 15v3M14 15v3M3 7h3M3 10h3M3 13h3M16 7h3M16 10h3M16 13h3" stroke="#444"/></svg>SOFTWARE</a>
</nav>

<section class="new-products panel abs">
  <div class="panel-title">NEW PRODUCTS</div>

  <article class="card feature abs" style="left:12px;top:44px;width:350px;height:249px">
    <div class="photo" role="img" aria-label="Living room wall with a flat TV and tall floor speakers" style="height:167px;background:linear-gradient(180deg,#b05a35,#8a4a2c 70%,#4a3426)">
      <div class="tags"><div class="tag">HOME</div><div class="tag">SPEAKERS</div></div>
    </div>
    <h3 class="card-title">Lorem Ipsum Dolor Sit Amet</h3>
    <div class="byline"><div class="avatar" role="img" aria-label="Author portrait"></div><span class="author">Evan Marlow</span><span class="posted">Posted On 11 Aug, 2016</span></div>
  </article>

  <article class="card mini abs" style="left:12px;top:310px;width:162px;height:174px">
    <div class="photo" role="img" aria-label="Hand pressing a smart home wall control panel" style="height:127px;background:linear-gradient(120deg,#c9b9a5,#e8e8e6 60%,#d6d8da)">
      <div class="tags"><div class="tag">HOME</div></div>
    </div>
    <h3 class="card-title">Lorem ipsum dolor sit amet, consectetuer elit</h3>
  </article>

  <article class="card mini abs" style="left:200px;top:310px;width:162px;height:174px">
    <div class="photo" role="img" aria-label="Smartphone and smartwatch product shot" style="height:127px;background:linear-gradient(120deg,#f3f3f3,#e2e4e6 55%,#f0a070 75%,#eef0f2)">
      <div class="tags"><div class="tag">HOME</div></div>
    </div>
    <h3 class="card-title">Lorem ipsum dolor sit amet, consectetuer elit</h3>
  </article>

  <article class="card feature abs" style="left:12px;top:506px;width:350px;height:249px">
    <div class="photo" role="img" aria-label="Black wireless speaker on a wooden table" style="height:168px;background:linear-gradient(110deg,#6b3d2c,#1e1f22 30%,#25272a 70%,#6a4a30)">
      <div class="tags"><div class="tag">AUDIO</div></div>
    </div>
    <h3 class="card-title">Lorem Ipsum Dolor Sit Amet</h3>
    <div class="byline"><div class="avatar" role="img" aria-label="Author portrait"></div><span class="author">Evan Marlow</span><span class="posted">Posted On 11 Aug, 2016</span></div>
  </article>
</section>

<section class="popular-products panel abs">
  <div class="panel-title">POPULAR PRODUCTS</div>
  <article class="card pop abs" style="left:11px;top:44px;width:156px;height:166px">
    <div class="photo" role="img" aria-label="Copper cookware set on a dark counter" style="height:118px;background:linear-gradient(160deg,#3a3533,#8a5a3a 55%,#2a2624)"><div class="tags" style="right:12px;bottom:10px"><div class="tag">HOME</div></div></div>
    <h3 class="card-title">Lorem ipsum dolor sit amet, consectetuer</h3>
  </article>
  <article class="card pop abs" style="left:11px;top:226px;width:156px;height:166px">
    <div class="photo" role="img" aria-label="Kitchen sink with chrome faucet and wooden cabinets" style="height:118px;background:linear-gradient(170deg,#e4e2de,#8a8b8e 45%,#a36b3a 70%,#c08447)"><div class="tags" style="right:12px;bottom:10px"><div class="tag">HOME</div></div></div>
    <h3 class="card-title">Lorem ipsum dolor sit amet, consectetuer</h3>
  </article>
  <article class="card pop abs" style="left:11px;top:408px;width:156px;height:166px">
    <div class="photo" role="img" aria-label="Tablet with keyboard cover and stylus" style="height:118px;background:linear-gradient(150deg,#a88a5a,#2a2c30 40%,#3a78c8 75%,#2b5aa0)"><div class="tags" style="right:12px;bottom:10px"><div class="tag">HOME</div></div></div>
    <h3 class="card-title">Lorem ipsum dolor sit amet, consectetuer</h3>
  </article>
  <article class="card pop abs" style="left:11px;top:590px;width:156px;height:166px">
    <div class="photo" role="img" aria-label="Keypad door lock on a wooden door" style="height:118px;background:linear-gradient(90deg,#7a98b8,#b8c6d4 40%,#d9dde1 60%,#8a6a44)"><div class="tags" style="right:12px;bottom:10px"><div class="tag">HOME</div></div></div>
    <h3 class="card-title">Lorem ipsum dolor sit amet, consectetuer</h3>
  </article>
</section>

<div class="load-more abs"><svg width="17" height="17" viewBox="0 0 17 17"><path d="M3 8.5a5.5 5.5 0 0 1 9.5-3.8M14 8.5a5.5 5.5 0 0 1-9.5 3.8" fill="none" stroke="#fff" stroke-width="1.5"/><path d="M12.8 1.8v3.2H9.6M4.2 15.2V12h3.2" fill="none" stroke="#fff" stroke-width="1.5"/></svg>Load More</div>

<footer class="site-footer abs">Copyright © 2016 Venlotix.com. All Rights Reserved.</footer>

</body>
</html>
```